4747 5858

Web(re)design of an existing directory search site www.le5858.be (in Dutch www.de4747.be and in English www.3838.be).

This site is a directory site, i.e. a "white pages" site whereby people can search the phone & details of another person based on a combination of name + city (for instance smith in Brussels); one can also search a company also based on a combination of name + city (for instance Vornak in Brussels); last but not least one can also search the name of the subscriber behind a specific telephone number (also called reverse search).

This site is quite outdated and needs a redesign, see instructions.

We need the output in XD format.

```html
<!DOCTYPE html>
<html lang="fr">
<head>
<meta charset="utf-8">
<title>4747 5858 – Renseignements</title>
<link href="https://fonts.googleapis.com/css2?family=Roboto+Condensed:wght@300;400;700&family=Roboto:wght@400&display=swap" rel="stylesheet">
<style>
  :root{
    --red:#d7141b;
    --red-dark:#b20d12;
    --ink:#333333;
    --muted:#555555;
    --band:#f2f2f2;
    --line:#c8c8c8;
    --faint:#ececec;
    --white:#ffffff;
  }
  *{box-sizing:border-box;margin:0;padding:0}
  html,body{width:1200px;height:600px;overflow:hidden;background:var(--white)}
  body{position:relative;font-family:"Roboto Condensed",Arial,sans-serif;color:var(--ink)}
  .band{position:absolute;left:0;width:1200px}
  .band-top{top:0;height:128px}
  .band-bottom{top:515px;height:85px}
  .brand{position:absolute;left:22px;top:44px;display:flex;align-items:center;gap:8px}
  .brand-dot{width:18px;height:18px;border-radius:50%;background:var(--red)}
  .brand-name{font-size:36px;font-weight:700;color:var(--red);letter-spacing:1px}
  .site-title{position:absolute;left:0;width:1200px;top:40px;text-align:center;font-weight:300;font-size:34px;color:#3a3a3a}
  .site-title em{font-style:normal;color:var(--red)}
  .lang{position:absolute;left:1098px;top:53px;font-size:17px;color:#444}
  .lang small{font-size:10px;margin-left:3px;vertical-align:2px}
  .menu{position:absolute;left:1155px;top:57px;width:23px}
  .menu span{display:block;height:2px;background:#333;margin-bottom:5px}
  .tabs{position:absolute;top:157px;left:0;width:1200px;display:flex;justify-content:center;font-size:19px;color:#3a3a3a}
  .tabs a{padding:0 23px;border-left:1px solid var(--line);line-height:18px;text-decoration:none;color:inherit}
  .tabs a:first-child{border-left:none}
  .tabs .active{color:var(--red)}
  .field{position:absolute;top:224px;width:262px;text-align:center}
  .field label{display:block;font-weight:700;font-size:16px;color:#333;height:30px}
  .field .input{height:42px;border:1px solid var(--line);border-radius:21px;background:var(--white)}
  .field .hint{margin-top:8px;font-size:12px;color:var(--muted)}
  .check{position:absolute;left:488px;top:347px;width:224px;height:54px;background:#f9f9f9;border:1px solid #e3e3e3;box-shadow:0 0 2px rgba(0,0,0,.08);font-family:Roboto,Arial,sans-serif}
  .check .box{position:absolute;left:9px;top:15px;width:21px;height:21px;border:2px solid #c1c1c1;border-radius:2px;background:var(--white)}
  .check .label{position:absolute;left:38px;top:20px;font-size:11px;color:#222}
  .check .mark{position:absolute;left:183px;top:9px;width:22px;height:22px;border-radius:50%;background:#c9d3e6}
  .check .service{position:absolute;right:8px;top:35px;font-size:7px;color:#555;text-align:center;line-height:9px}
  .search-btn{position:absolute;left:540px;top:427px;width:120px;height:42px;border-radius:21px;border:none;background:linear-gradient(var(--red),var(--red-dark));color:var(--white);font-family:inherit;font-weight:700;font-size:19px}
  .watermark{position:absolute;left:1005px;top:335px}
  .footer-links{position:absolute;left:171px;top:536px;font-size:14px;color:#3a3a3a;display:flex}
  .footer-links a{color:inherit;text-decoration:none;padding:0 10px;border-left:1px solid var(--line);line-height:14px}
  .footer-links a:first-child{padding-left:0;border-left:none}
  .copyright{position:absolute;left:171px;top:558px;font-size:14px;color:#3a3a3a}
  .partner-badge{position:absolute;left:940px;top:530px;width:64px;height:54px;border-radius:8px;background:#e2e2e2}
</style>
</head>
<body>
  <svg class="band band-top" width="1200" height="128" aria-hidden="true">
    <polygon points="308,0 1200,0 1200,128 180,128" fill="var(--band)"/>
  </svg>
  <svg class="band band-bottom" width="1200" height="85" aria-hidden="true">
    <polygon points="0,0 813,0 898,85 0,85" fill="var(--band)"/>
  </svg>

  <header>
    <div class="brand"><span class="brand-dot"></span><span class="brand-name">47·47</span></div>
    <h1 class="site-title">Les Renseignements <em>QUARANTE-SEPT</em> Utiles</h1>
    <div class="lang">FR<small>∨</small></div>
    <div class="menu"><span></span><span></span><span></span></div>
  </header>

  <nav class="tabs">
    <a class="active">Particuliers</a>
    <a>Sociétés</a>
    <a>Annuaire inversé</a>
    <a>International</a>
  </nav>

  <div class="field" style="left:173px"><label>Nom de famille:</label><div class="input"></div><div class="hint">Ex: Dupont, Janssens, ...</div></div>
  <div class="field" style="left:469px"><label>Prénom:</label><div class="input"></div><div class="hint">Ex: Jan, Louis, ...</div></div>
  <div class="field" style="left:764px"><label>Localité:</label><div class="input"></div><div class="hint">Ex: Liége, Anvers, 1150, ....</div></div>

  <div class="check">
    <span class="box"></span>
    <span class="label">I'm not a robot</span>
    <span class="mark"></span>
    <div class="service">VeriCheck<br>Privacy - Terms</div>
  </div>

  <button class="search-btn">47-47!</button>

  <div class="watermark" aria-hidden="true">
    <svg width="175" height="155">
      <circle cx="14" cy="78" r="12" fill="var(--faint)"/>
      <text x="34" y="98" font-family="Roboto Condensed, sans-serif" font-weight="700" font-size="62" fill="var(--faint)">47·47</text>
    </svg>
  </div>

  <footer>
    <div class="footer-links">
      <a>B2B Services</a><a>Aide</a><a>Conditions générales d'utilisation</a><a>Respect de la vie privée</a>
    </div>
    <div class="copyright">Copyright Orvanel 2022, tous droits réservés.</div>
    <div class="partner-badge" role="img" aria-label="Badge partenaire"></div>
  </footer>
</body>
</html>
```